Healthcare/Medical Consultant Company

QRN is a Healthcare Conultant Company. We help doctors manage the business side of their medical practice.
We already have a very basic world press design. We want an upgraded design that conveys partnership, healthcare expertise and healthcare innovation to our client. It needs to have a sleek, clean, modern and inclusive look. Pictures need need to convey diversity (including pictures of people of all races and shows both men and women working together in a healthcare environment to make it better). The Pictures on the home page should particularly illustrate diversity and Healthcare expertise. The company logo is blue and white but the site doesn’t have to follow the exact same theme but the logo needs to blend well with the chosen theme. The logo should ideally be in the header of the website. We would also like the following included in our website:

1. Pages should include: a home page, About Us page, Services page, Get a quote page, Contact Us page, Staff page(where we can add pictures and bio for staff).

2. The Drop down menu for services should have hyperlinks ( for each service)Leading to a page that provides detailed info about that specific service. Our services include: Revenue Cycle Management, Regulatory Compliance, Human Resources Management, & practice Management.

3. Links to social media should in the header or footer of each page.

4. Contact info should be in the footer of each page.

5. Clients should be an email to us from the contact page.

Target Market(s)

Physician Medical Practices

Industry/Entity Type

Medical

Coding

Coded - Design and coding required

Font styles to use
Sans Serif

Colors

Designer to choose colors to be used in the design.

Requirements
Must have
• See project description
Nice to have
• See project description

```html
<!DOCTYPE html>
<html lang="en">
<head>
<meta charset="utf-8">
<title>QRN — Quarterline Health Partners</title>
<link href="https://fonts.googleapis.com/css2?family=Lato:ital,wght@0,400;0,700;0,900;1,400;1,700&display=swap" rel="stylesheet">
<style>
:root{
  --navy:#0c3f8c;
  --blue:#1a72c2;
  --sky:#2a8fd6;
  --orange:#e05a10;
  --ink:#333a44;
  --white:#ffffff;
  --bar:#0b3784;
}
*{margin:0;padding:0;box-sizing:border-box}
html,body{width:1200px;height:2679px;overflow:hidden}
body{font-family:'Lato',sans-serif;color:var(--ink);background:var(--white);position:relative}
.abs{position:absolute}
.topline{position:absolute;left:0;top:0;width:1200px;height:5px;background:var(--blue)}

/* header */
.site-header{position:absolute;left:0;top:0;width:1200px;height:130px}
.brand{position:absolute;left:75px;top:30px;font-weight:900;font-size:44px;color:var(--navy);letter-spacing:2px;line-height:1}
.brand-sub{position:absolute;left:75px;top:80px;font-size:13px;font-weight:700;color:var(--navy)}
.social{position:absolute;display:flex;gap:18px}
.social span{display:block;width:22px;height:22px;border-radius:50%;background:var(--ink)}
.header-social{left:716px;top:33px}
.quote-btn{position:absolute;left:934px;top:21px;width:193px;height:46px;background:linear-gradient(#1c78c8,#0f5aa8);color:#fff;font-weight:700;font-size:16px;display:flex;align-items:center;justify-content:center;gap:10px;border-radius:2px}
.main-nav{position:absolute;top:86px;left:0;width:1200px;font-size:14px;font-weight:700;color:var(--ink)}
.main-nav a{position:absolute;text-decoration:none;color:inherit;white-space:nowrap}
.main-nav .current{color:var(--navy)}
.nav-curve{position:absolute;left:622px;top:113px}

/* hero */
.hero{position:absolute;left:0;top:130px;width:1200px;height:547px;
  background:linear-gradient(100deg,#3e4a55 0%,#6f7780 35%,#a6a9ad 60%,#d7d4cf 80%,#8d8a86 100%)}
.hero-shade{position:absolute;inset:0;background:rgba(20,30,45,.35)}
.hero h1{position:absolute;top:218px;width:1200px;text-align:center;color:#fff;font-size:48px;font-weight:700;letter-spacing:.5px}
.hero h2{position:absolute;top:280px;width:1200px;text-align:center;color:#fff;font-size:33px;font-weight:700}
.dots{position:absolute;top:487px;left:566px;display:flex;gap:9px}
.dots span{width:10px;height:10px;border-radius:50%;background:#fff}
.dots span:first-child{background:var(--blue)}

/* headings */
.section-title{position:absolute;width:1200px;text-align:center;font-size:27px;font-weight:900;color:var(--navy)}
.title-curve{position:absolute;left:545px}

/* about */
.about-text{position:absolute;left:90px;top:816px;width:1020px;text-align:center;font-size:15px;line-height:25px;color:var(--ink)}
.btn-orange{position:absolute;background:var(--orange);color:#fff;font-weight:700;display:flex;align-items:center;justify-content:center;font-size:14px}

/* services */
.services{position:absolute;left:0;top:1027px;width:1200px;height:505px;
  background:linear-gradient(120deg,#2a86cf 0%,#1566b4 45%,#0f4f9f 75%,#1a6bbb 100%)}
.service-label{position:absolute;color:#fff;font-size:16px;font-weight:900;line-height:25px}
.left-label{text-align:right}
.hub-name{position:absolute;left:482px;top:1270px;width:236px;text-align:center;color:var(--navy);font-weight:900;font-size:42px;letter-spacing:2px}
.hub-sub{position:absolute;left:482px;top:1318px;width:236px;text-align:center;color:var(--navy);font-size:12px;font-weight:700}

/* blog */
.card{position:absolute;top:1690px;width:330px}
.card-img{width:330px;height:180px}
.card h3{margin-top:16px;font-size:16px;font-weight:900;color:var(--navy)}
.card time{display:block;margin-top:7px;font-size:14px;color:var(--sky);font-weight:700}
.card p{margin-top:10px;font-size:14px;line-height:23px}
.card a{display:block;margin-top:9px;font-size:14px;font-style:italic;font-weight:700;color:var(--navy);text-decoration:none}

/* newsletter */
.newsletter{position:absolute;left:0;top:2111px;width:1200px;height:230px;
  background:linear-gradient(110deg,#1a64b2 0%,#2b80c9 50%,#5ea2d8 100%)}
.newsletter h2{position:absolute;top:46px;width:1200px;text-align:center;color:#fff;font-size:22px;font-weight:700}
.newsletter p{position:absolute;top:88px;width:1200px;text-align:center;color:#fff;font-size:14px}
.email-field{position:absolute;left:343px;top:125px;width:464px;height:45px;background:#fff;font-size:13px;color:#555;padding-left:16px;display:flex;align-items:center}
.go{position:absolute;left:807px;top:125px;width:50px;height:45px;background:var(--orange);color:#fff;font-weight:900;font-size:16px;display:flex;align-items:center;justify-content:center}

/* footer */
.footer-col{position:absolute;top:2390px;font-size:13.5px;line-height:27.7px}
.footer-col h4{font-size:17px;font-weight:700;color:var(--sky);margin-bottom:6px;line-height:24px}
.footer-col ul{list-style:none}
.footer-about{position:absolute;left:75px;top:2472px;width:250px;font-size:13.5px;line-height:23px}
.footer-about a{color:var(--navy);font-weight:700;text-decoration:none}
.contact-row{display:flex;align-items:center;gap:18px}
.bottom-bar{position:absolute;left:0;top:2622px;width:1200px;height:57px;background:var(--bar);color:#fff}
.bottom-bar p{position:absolute;left:75px;top:20px;font-size:12px}
.footer-social{right:75px;top:17px}
.footer-social span{background:#fff}
</style>
</head>
<body>

<div class="topline"></div>

<header class="site-header">
  <div class="brand">QRN</div>
  <div class="brand-sub">Quarterline Health Partners LLC</div>
  <div class="social header-social" aria-label="Social media links">
    <span></span><span></span><span></span><span></span><span></span>
  </div>
  <div class="quote-btn">GET A QUOTE
    <svg width="10" height="14" viewBox="0 0 10 14"><path d="M2 1l6 6-6 6" stroke="#fff" stroke-width="2.6" fill="none"/></svg>
  </div>
  <nav class="main-nav">
    <a class="current" style="left:634px">HOME</a>
    <a style="left:724px">ABOUT US</a>
    <a style="left:840px">SERVICES</a>
    <a style="left:951px">STAFF</a>
    <a style="left:1038px">CONTACT US</a>
  </nav>
  <svg class="nav-curve" width="70" height="10" viewBox="0 0 70 10"><path d="M2 8 Q35 -2 68 8" stroke="var(--navy)" stroke-width="2" fill="none"/></svg>
</header>

<section class="hero" role="img" aria-label="Photo of two colleagues, a man and a woman, reviewing reports together at an office desk">
  <div class="hero-shade"></div>
  <h1>QUARTERLINE HEALTH PARTNERS</h1>
  <h2>ADVANCING HEALTHCARE</h2>
  <div class="dots"><span></span><span></span><span></span><span></span></div>
</section>

<h2 class="section-title" style="top:730px">ABOUT OUR COMPANY</h2>
<svg class="title-curve" style="top:776px" width="110" height="14" viewBox="0 0 110 14"><path d="M2 12 Q55 -4 108 12" stroke="var(--navy)" stroke-width="3" fill="none"/></svg>
<p class="about-text">Quarterline Health Partners (QRN) is a healthcare consulting firm skilled at helping physician practices advance their strategic vision in an ever-evolving healthcare system. Quarterline Health Partners specializes in revenue cycle optimization, practice management improvement and developing new physician practices.</p>
<div class="btn-orange" style="left:523px;top:922px;width:152px;height:44px">READ MORE</div>

<section class="services" role="img" aria-label="Blue-toned photo of a calculator and stethoscope on medical paperwork"></section>
<h2 class="section-title" style="top:1082px;color:#fff">OUR SERVICES</h2>
<svg class="title-curve" style="top:1128px" width="110" height="14" viewBox="0 0 110 14"><path d="M2 12 Q55 -4 108 12" stroke="#fff" stroke-width="3" fill="none"/></svg>

<svg class="abs" style="left:0;top:0" width="1200" height="1532" viewBox="0 0 1200 1532">
  <g stroke="rgba(255,255,255,.75)" stroke-width="2" fill="none">
    <polyline points="439,1197 490,1197 515,1222"/>
    <polyline points="386,1300 482,1300"/>
    <polyline points="439,1402 490,1402 515,1377"/>
    <polyline points="761,1197 710,1197 685,1222"/>
    <polyline points="813,1300 718,1300"/>
    <polyline points="761,1402 710,1402 685,1377"/>
  </g>
  <circle cx="600" cy="1298" r="118" fill="#fff"/>
  <g fill="var(--sky)" stroke="#fff" stroke-width="3">
    <circle cx="405" cy="1197" r="34"/><circle cx="352" cy="1300" r="34"/><circle cx="405" cy="1402" r="34"/>
    <circle cx="795" cy="1197" r="34"/><circle cx="847" cy="1300" r="34"/><circle cx="795" cy="1402" r="34"/>
  </g>
  <!-- refresh -->
  <g stroke="#fff" stroke-width="3" fill="none">
    <path d="M393 1192 a13 13 0 0 1 23 -5"/><path d="M417 1202 a13 13 0 0 1 -23 5"/>
  </g>
  <path d="M418 1180 v9 h-9z M392 1214 v-9 h9z" fill="#fff"/>
  <!-- org chart -->
  <g fill="#fff"><rect x="346" y="1286" width="12" height="9"/><rect x="336" y="1307" width="9" height="8"/><rect x="348" y="1307" width="9" height="8"/><rect x="360" y="1307" width="9" height="8"/></g>
  <path d="M352 1295v6 M340 1307v-6h24v6 M352 1301v6" stroke="#fff" stroke-width="2" fill="none"/>
  <!-- person -->
  <circle cx="405" cy="1392" r="7" fill="#fff"/><path d="M391 1416 q0 -14 14 -14 q14 0 14 14z" fill="#fff"/>
  <!-- people -->
  <g fill="#fff"><circle cx="795" cy="1188" r="6"/><circle cx="782" cy="1192" r="5"/><circle cx="808" cy="1192" r="5"/>
  <path d="M784 1210 q0-13 11-13 q11 0 11 13z"/><path d="M772 1208 q0-10 10-10 q4 0 6 2 q-5 4 -5 8z"/><path d="M818 1208 q0-10 -10-10 q-4 0 -6 2 q5 4 5 8z"/></g>
  <!-- document -->
  <path d="M837 1285h14l8 8v22h-22z" fill="#fff"/><path d="M842 1300h12M842 1306h12" stroke="var(--sky)" stroke-width="2"/>
  <!-- laptop -->
  <rect x="781" y="1391" width="28" height="18" rx="1" fill="none" stroke="#fff" stroke-width="3"/><rect x="775" y="1410" width="40" height="4" fill="#fff"/>
</svg>
<div class="hub-name">QRN</div>
<div class="hub-sub">Quarterline Health Partners LLC</div>

<div class="service-label left-label" style="left:100px;width:243px;top:1169px">REVENUE<br>CYCLE MANAGEMENT</div>
<div class="service-label left-label" style="left:40px;width:265px;top:1275px">REGULATORY &amp;<br>COMPLIANCE MANAGEMENT</div>
<div class="service-label left-label" style="left:100px;width:243px;top:1384px">PRACTICE<br>MANAGEMENT</div>
<div class="service-label" style="left:856px;top:1169px">HUMAN RESOURCES<br>MANAGEMENT</div>
<div class="service-label" style="left:904px;top:1275px">MEDICAL BILLING<br>&amp; CODING</div>
<div class="service-label" style="left:856px;top:1384px">STAFF EDUCATION &amp;<br>TRAINING</div>

<h2 class="section-title" style="top:1582px">BLOG POSTS</h2>
<svg class="title-curve" style="top:1628px" width="110" height="14" viewBox="0 0 110 14"><path d="M2 12 Q55 -4 108 12" stroke="var(--navy)" stroke-width="3" fill="none"/></svg>

<article class="card" style="left:75px">
  <div class="card-img" role="img" aria-label="Blue-toned image of a hand holding a glowing shield symbol for health protection" style="background:linear-gradient(120deg,#9cc3e6,#3a78bb 55%,#1d4f8f)"></div>
  <h3>ALIQUAM MOLESTIE MI ET IMPERDIET</h3>
  <time>Aug 25, 2018</time>
  <p>Euismod, dui purus auctor tellus, et interdum lacus lectus et ante. Sed accumsan sollicitudin sapien, sit ame neque ac lobortis..</p>
  <a>Read More</a>
</article>
<article class="card" style="left:434px">
  <div class="card-img" role="img" aria-label="Photo of a diverse team of professionals meeting around a conference table" style="background:linear-gradient(120deg,#dcd8cf,#a7a39b 50%,#4d5866)"></div>
  <h3>ALIQUAM MOLESTIE MI ET IMPERDIET</h3>
  <time>Aug 25, 2018</time>
  <p>Euismod, dui purus auctor tellus, et interdum lacus lectus et ante. Sed accumsan sollicitudin sapien, sit ame neque ac lobortis..</p>
  <a>Read More</a>
</article>
<article class="card" style="left:795px">
  <div class="card-img" role="img" aria-label="Photo of a hand using a tablet beside a stethoscope" style="background:linear-gradient(120deg,#e9edf1,#8fa6bd 50%,#34506f)"></div>
  <h3>ALIQUAM MOLESTIE MI ET IMPERDIET</h3>
  <time>Aug 25, 2018</time>
  <p>Euismod, dui purus auctor tellus, et interdum lacus lectus et ante. Sed accumsan sollicitudin sapien, sit ame neque ac lobortis..</p>
  <a>Read More</a>
</article>

<section class="newsletter" role="img" aria-label="Blue-toned photo of a clinician holding a stethoscope">
  <h2>SUBSCRIBE TO OUR NEWSLETTER</h2>
  <p>Vestibulum ante ipsum primis in &nbsp;faucibus orci luctus et ultrices &nbsp;posuere cubilia.</p>
  <div class="email-field">Enter Email Address</div>
  <div class="go">GO</div>
</section>

<footer>
  <div class="brand" style="top:2398px;font-size:40px">QRN</div>
  <div class="brand-sub" style="top:2444px;font-size:11px">Quarterline Health Partners LLC</div>
  <p class="footer-about">You might be an artist who would like to introduce yourself and your work here or maybe you’re a business with a mission to describe.<br><a>Read More</a></p>

  <div class="footer-col" style="left:379px">
    <h4>QUICK LINKS</h4>
    <ul><li>Home</li><li>About Us</li><li>Services</li><li>Staff</li><li>Get a Quote</li><li>Contact Us</li></ul>
  </div>
  <div class="footer-col" style="left:604px">
    <h4>SERVICES</h4>
    <ul><li>Revenue Cycle Management</li><li>Medical Billing &amp; Coding</li><li>Regulatory Compliance</li><li>Human Resources Training</li><li>Staff Education &amp; Training</li></ul>
  </div>
  <div class="footer-col" style="left:884px">
    <h4>CONTACT INFO</h4>
    <div>318 Harlow Street Brookfield, NY 10452</div>
    <div class="contact-row"><svg width="14" height="14" viewBox="0 0 24 24"><path d="M6 2l4 4-2 3c1 3 4 6 7 7l3-2 4 4-3 4C10 22 2 14 2 5z" fill="var(--ink)"/></svg>(555)-214-0387</div>
    <div class="contact-row"><svg width="14" height="12" viewBox="0 0 24 18"><rect width="24" height="18" fill="var(--ink)"/><path d="M0 0l12 10L24 0" stroke="#fff" stroke-width="2" fill="none"/></svg>info@quarterlinehealth.com</div>
    <h4 style="margin-top:20px">HOURS</h4>
    <div>Monday—Friday: &nbsp;&nbsp;9:00AM–5:00PM</div>
  </div>

  <div class="bottom-bar">
    <p>Copyright © 2018 Company Name. All Right Reserved</p>
    <div class="social footer-social abs" aria-label="Social media links">
      <span></span><span></span><span></span><span></span><span></span>
    </div>
  </div>
</footer>

</body>
</html>
```